Birchline Septic Solutions

Would like to see some single sided ones but would also like to see some double sided with one sided only being the logo. Owners name is Colin Vandro. Phone number is 555-214-0387
Services are pumping, inspections, installs, and repairs

Contact Information for Business Card

555-241-0387 Colin Vandro Elmcrest, OH

```html
<!DOCTYPE html>
<html lang="en">
<head>
<meta charset="utf-8">
<title>Birchline Septic Solutions – Business Card</title>
<link href="https://fonts.googleapis.com/css2?family=Montserrat:wght@600;700;800&display=swap" rel="stylesheet">
<style>
  :root {
    --stage: #e6ddd0;
    --card-frost: #eceae6;
    --card-frost-edge: #f7f6f3;
    --ink: #1d1b1a;
    --band: #1a1716;
    --teal: #1f9f86;
    --teal-bright: #22b39a;
    --cream: #e8dccb;
    --tan: #a68c78;
  }
  * { margin: 0; padding: 0; box-sizing: border-box; }
  html, body { width: 1200px; height: 897px; overflow: hidden; }
  body {
    background: var(--stage);
    font-family: "Montserrat", Arial, sans-serif;
    position: relative;
  }
  .business-card {
    position: absolute;
    left: 100px; top: 168px;
    width: 1000px; height: 560px;
    border-radius: 22px;
    overflow: hidden;
    background: linear-gradient(135deg, var(--card-frost-edge), var(--card-frost) 60%, #e2dfda);
    box-shadow: 0 18px 40px rgba(60, 45, 30, 0.18);
  }
  .card-band { position: absolute; inset: 0; width: 100%; height: 100%; }
  .brand {
    position: absolute;
    left: 0; right: 0; top: 120px;
    text-align: center;
    color: var(--ink);
    font-weight: 800;
  }
  .brand-name {
    display: block;
    font-size: 78px;
    letter-spacing: 2px;
    line-height: 1;
  }
  .brand-tagline {
    display: block;
    margin-top: 22px;
    font-size: 21px;
    letter-spacing: 7px;
  }
  .owner {
    position: absolute;
    right: 535px; top: 420px;
    text-align: right;
  }
  .owner-name {
    font-size: 42px;
    font-weight: 700;
    color: var(--teal);
    line-height: 1;
    letter-spacing: 0.5px;
  }
  .owner-town {
    margin-top: 12px;
    font-size: 24px;
    font-weight: 600;
    color: var(--tan);
  }
  .divider {
    position: absolute;
    left: 502px; top: 422px;
    width: 2px; height: 78px;
    background: var(--teal);
  }
  .phone {
    position: absolute;
    left: 540px; top: 438px;
    display: flex; align-items: center; gap: 14px;
    font-size: 34px;
    font-weight: 600;
    color: var(--cream);
  }
  .phone-icon { width: 30px; height: 24px; }
</style>
</head>
<body>
  <section class="business-card">
    <svg class="card-band" viewBox="0 0 1000 560" preserveAspectRatio="none" aria-hidden="true">
      <path d="M0,392 Q420,270 660,302 Q560,292 0,412 Z" fill="var(--band)"/>
      <path d="M0,418 Q470,258 1000,432 L1000,560 L0,560 Z" fill="var(--band)"/>
      <path d="M0,412 Q470,250 1000,424 L1000,432 Q470,258 0,418 Z" fill="var(--cream)"/>
      <path d="M270,338 Q620,265 1000,422 L1000,428 Q620,275 270,338 Z" fill="var(--teal-bright)"/>
    </svg>

    <div class="brand">
      <span class="brand-name">BIRCHLINE</span>
      <span class="brand-tagline">SEPTIC SOLUTIONS</span>
    </div>

    <div class="owner">
      <p class="owner-name">COLIN VANDRO</p>
      <p class="owner-town">Elmcrest, OH</p>
    </div>

    <div class="divider"></div>

    <div class="phone">
      <svg class="phone-icon" viewBox="0 0 30 24" aria-hidden="true">
        <path d="M2,8 Q15,-1 28,8 L25,11 L21,9 L21,6 Q15,4 9,6 L9,9 L5,11 Z" fill="var(--teal)"/>
        <path d="M8,11 L22,11 L27,22 L3,22 Z" fill="var(--teal)"/>
        <circle cx="15" cy="16" r="3" fill="var(--band)"/>
      </svg>
      <span>555-241-0387</span>
    </div>
  </section>
</body>
</html>
```